Business Card for Professional Photographer

I'm looking for an eye catching modern clean design that compliments my logo/ website fonts & colours.
I specialise in architecture, corporate & commercial photography so I'm marketing to professional clients rather than portrait / wedding clients.

I would prefer to not have a solid black design.

My logo brand guide is as follows :

Main front font. : Reislust
Main font colour : #fff
Slogan front font : Ubuntu Bold
Monogram front font : Venti Medium
Container colour : #fff

I need print ready files in pdf .png & .eps formats.

Included in the files below are some screen grabs as reference to font & colours etc.

```html
<!DOCTYPE html>
<html lang="en">
<head>
<meta charset="utf-8">
<title>Mark Hadley – Business Card</title>
<link rel="stylesheet" href="https://fonts.googleapis.com/css2?family=Fjalla+One&family=Roboto:wght@400&display=swap">
<style>
  :root {
    --page-bg: #d9d4cc;
    --frost: #efebe4;
    --frost-edge: #f7f4ef;
    --gold-deep: #d6b064;
    --gold-mid: #e6c987;
    --gold-light: #f1dfae;
    --gold-line: #e9cf86;
    --brand-mark: #d9b866;
    --ink: #1e1b17;
    --brand-ink: #3a3836;
  }
  * { margin: 0; padding: 0; box-sizing: border-box; }
  html, body {
    width: 1200px; height: 1054px; overflow: hidden;
    background: var(--page-bg);
  }
  .card {
    position: absolute; left: 100px; top: 224px;
    width: 1000px; height: 605px;
    background: linear-gradient(160deg, var(--frost-edge), var(--frost));
    border-radius: 4px;
    box-shadow: 0 12px 40px rgba(0,0,0,.18);
    overflow: hidden;
    font-family: "Roboto", sans-serif;
    color: var(--ink);
  }
  .card__panel { position: absolute; inset: 0; width: 100%; height: 100%; }
  .holder { position: absolute; left: 56px; top: 66px; }
  .holder__name {
    font-family: "Fjalla One", sans-serif;
    font-size: 38px; line-height: 1.1; letter-spacing: .2px;
  }
  .holder__role { font-size: 25px; margin-top: 6px; }
  .contacts { position: absolute; left: 56px; top: 380px; list-style: none; }
  .contacts__item {
    display: flex; align-items: center; gap: 24px;
    font-size: 25px; height: 38px;
  }
  .contacts__icon { width: 24px; height: 24px; fill: var(--ink); flex: none; }
  .contacts__address { font-size: 25px; margin-top: 12px; }
  .brand {
    position: absolute; left: 560px; width: 390px; top: 170px;
    display: flex; flex-direction: column; align-items: center;
  }
  .brand__dot {
    width: 170px; height: 170px; border-radius: 50%;
    background: var(--brand-mark);
  }
  .brand__name {
    margin-top: 46px;
    font-family: "Roboto", sans-serif; font-weight: 400;
    font-size: 34px; color: var(--brand-ink);
    white-space: nowrap;
  }
</style>
</head>
<body>
  <div class="card">
    <svg class="card__panel" viewBox="0 0 1000 605" preserveAspectRatio="none" aria-hidden="true">
      <defs>
        <linearGradient id="goldFill" x1="0" y1="0" x2="1" y2="1">
          <stop offset="0" stop-color="var(--gold-deep)"/>
          <stop offset=".55" stop-color="var(--gold-mid)"/>
          <stop offset="1" stop-color="var(--gold-light)"/>
        </linearGradient>
      </defs>
      <path d="M0 0 H568 C500 160 500 440 548 605 H0 Z" fill="url(#goldFill)"/>
      <path d="M568 0 C500 160 500 440 548 605 H562 C514 440 514 160 582 0 Z" fill="var(--gold-line)" opacity=".7"/>
    </svg>

    <div class="holder">
      <div class="holder__name">Mark Hadley</div>
      <div class="holder__role">Photographer</div>
    </div>

    <ul class="contacts">
      <li class="contacts__item">
        <svg class="contacts__icon" viewBox="0 0 24 24"><path d="M3 9c0-3 4-5 9-5s9 2 9 5v2h-5V9c-1-1-7-1-8 0v2H3z M6 13h12l2 7H4z"/></svg>
        <span>0412555087</span>
      </li>
      <li class="contacts__item">
        <svg class="contacts__icon" viewBox="0 0 24 24"><path d="M2 5h20v14H2z M4 7v1l8 5 8-5V7l-8 5z" fill-rule="evenodd"/></svg>
        <span>hello@clearlinestudio.com.au</span>
      </li>
      <li class="contacts__item">
        <svg class="contacts__icon" viewBox="0 0 24 24"><path d="M12 2a10 10 0 1 0 0 20a10 10 0 1 0 0-20z M4 11h4c0-3 1-5 2-7a8 8 0 0 0-6 7z M10 11h4c0-3-1-5-2-7c-1 2-2 4-2 7z M16 11h4a8 8 0 0 0-6-7c1 2 2 4 2 7z M4 13a8 8 0 0 0 6 7c-1-2-2-4-2-7z M10 13c0 3 1 5 2 7c1-2 2-4 2-7z M16 13c0 3-1 5-2 7a8 8 0 0 0 6-7z" fill-rule="evenodd"/></svg>
        <span>www.clearlinestudio.com.au</span>
      </li>
      <li class="contacts__address">48 Harbour Rd Warrnambool Vic 3280</li>
    </ul>

    <div class="brand">
      <div class="brand__dot" aria-hidden="true"></div>
      <div class="brand__name">Clear Line Studio</div>
    </div>
  </div>
</body>
</html>
```